Motel Sign - Front

(21/03/12 - I've edited the brief and removing the words "garden view" its not fitting in the designs I'm getting and just want the word motel to be the focus. I have a template/vision of what I want - see the whiteboard sketch of what I'm looking for uploaded today. Definitely open to creatively, new designs and different ideas but the whiteboard design I've done should be a guideline. Keep it fresh/green/white. use the sample photos of green as inspiration. Thanks)
We are a motel set in the mountain country of Victoria - Australia. The front of the motel needs a fresh look. We recently removed a large amount of the garden to expose a brick courtyard fence which the front of the courtyard faces out to the main road. Within the courtyard fence there is a wooden frame and paneling.
We want to have a new sign created to slot into the wooden frame. (see photo) its the white component.
Its a very large and unusual shape and I want to keep it simple but need to fill the in the best way possible.
The space is 940mm high and 4940mm width.
The message of the sign is simple the word "MOTEL". I want people to be able to drive past and glance in and see we are a motel straight away. So the main purpose of the sign is to say "MOTEL".
I am open to colour use to match the space and have impact. I thought a background colour should be 'off white'. I'm open to the colours used to match your design as long as it matches the brief. Maybe a garden green for the emblem.
IN BRIEF:
1) the word "MOTEL"
2) Border/Background that ties in the garden.
The design should be centred, clean and simple, doesn't have to fill the whole space as long as its balanced and centred.
I like cursive and garden like designs for this one - as long its the word MOTEL still has impact. (OPEN TO NEW IDEAS)
I am also open to different ideas and suggestions if you feel you have a better way to take advantage of this space.
The sign will be 7-8 metres from the road itself.
NOTE: the photos show the space and the painted white in the space where the sign will go. The garden in front of this space will be completely cleared.
Motel

```html
<!DOCTYPE html>
<html lang="en">
<head>
<meta charset="utf-8">
<title>Motel Sign – Front</title>
<link rel="stylesheet" href="https://fonts.googleapis.com/css2?family=Tinos:wght@700&display=swap">
<style>
  :root {
    --page-bg: #f4f5f0;
    --green-deep: #0f8a3a;
    --green-mid: #1fa24a;
    --green-light: #3dbb5e;
    --letter-white: #ffffff;
    --letter-edge: #0b4a22;
  }
  * { margin: 0; padding: 0; box-sizing: border-box; }
  html, body {
    width: 1200px;
    height: 857px;
    overflow: hidden;
    background: var(--page-bg);
  }
  .canvas {
    position: relative;
    width: 1200px;
    height: 857px;
    display: flex;
    align-items: center;
    justify-content: center;
  }
  .sign {
    position: relative;
    width: 1100px;
    height: 209px;
    display: flex;
    align-items: center;
    justify-content: center;
  }
  .sign-clover-field {
    position: absolute;
    inset: 0;
    background:
      radial-gradient(ellipse at 15% 30%, rgba(90, 210, 120, 0.35), transparent 45%),
      radial-gradient(ellipse at 85% 70%, rgba(90, 210, 120, 0.3), transparent 45%),
      linear-gradient(180deg, var(--green-mid) 0%, var(--green-deep) 55%, var(--green-mid) 100%);
  }
  .sign-word {
    position: relative;
    font-family: "Tinos", "Times New Roman", serif;
    font-weight: 700;
    font-size: 160px;
    line-height: 1;
    letter-spacing: 0.3em;
    margin-right: -0.3em;
    color: var(--letter-white);
    -webkit-text-stroke: 2px var(--letter-edge);
    paint-order: stroke fill;
    text-shadow: 3px 4px 4px rgba(5, 50, 20, 0.6);
  }
</style>
</head>
<body>
  <main class="canvas">
    <section class="sign">
      <div class="sign-clover-field" role="img" aria-label="Green background with a soft pattern of clover leaves"></div>
      <h1 class="sign-word">MOTEL</h1>
    </section>
  </main>
</body>
</html>
```